Birchline Septic Solutions

Would like to see some single sided ones but would also like to see some double sided with one sided only being the logo. Owners name is Colin Vandro. Phone number is 555-214-0387
Services are pumping, inspections, installs, and repairs

Contact Information for Business Card

555-241-0387 Colin Vandro Millbrook, OH

```html
<!DOCTYPE html>
<html lang="en">
<head>
<meta charset="utf-8">
<title>Birchline Septic Solutions – Business Cards</title>
<link rel="stylesheet" href="https://fonts.googleapis.com/css2?family=Jost:wght@400;500;600&display=swap">
<style>
  :root {
    --page-bg: #e4e5e7;
    --card-bg: #ffffff;
    --ink: #111111;
    --ink-soft: #3a3a3a;
    --teal: #3cc4bd;
    --scene-dark: #0e0e0e;
    --scene-mid: #2b2b2b;
  }
  * { box-sizing: border-box; margin: 0; padding: 0; }
  html, body {
    width: 1200px; height: 800px; overflow: hidden;
    background: var(--page-bg);
    font-family: "Jost", "Futura", sans-serif;
    color: var(--ink);
  }
  .canvas {
    width: 1200px; height: 800px;
    display: flex; align-items: center; justify-content: center; gap: 40px;
  }
  .card {
    position: relative;
    width: 540px; height: 309px;
    background: var(--card-bg);
    overflow: hidden;
    box-shadow: 0 6px 18px rgba(0,0,0,0.12);
  }
  .scene {
    position: absolute;
    background: linear-gradient(160deg, var(--scene-mid), var(--scene-dark));
  }
  .brand-name {
    font-weight: 600;
    color: var(--ink);
    text-transform: uppercase;
    letter-spacing: 0.12em;
    line-height: 1.25;
  }
  .divider {
    position: absolute;
    width: 1.5px;
    background: var(--teal);
  }

  /* Front */
  .card-front .scene { left: 0; right: 0; top: 170px; bottom: 0; }
  .card-front .brand-name { position: absolute; left: 36px; top: 48px; width: 220px; font-size: 22px; }
  .card-front .divider { left: 282px; top: 36px; height: 110px; }
  .contact { position: absolute; left: 302px; top: 44px; }
  .contact-name { font-size: 19px; font-weight: 500; text-transform: uppercase; letter-spacing: 0.02em; }
  .contact-role { font-size: 13px; color: var(--ink-soft); margin-bottom: 14px; }
  .contact-line { display: flex; align-items: center; gap: 7px; font-size: 14px; color: var(--ink-soft); margin-bottom: 5px; }
  .contact-line svg { width: 12px; height: 12px; fill: var(--teal); }

  /* Back */
  .card-back .scene { left: 0; top: 0; bottom: 0; width: 200px; }
  .services { position: absolute; right: 210px; top: 70px; text-align: right; }
  .services-title { font-size: 14px; font-weight: 500; text-transform: uppercase; margin-bottom: 6px; }
  .services-list { list-style: none; font-size: 13px; color: var(--ink-soft); line-height: 1.35; }
  .services-list li::after { content: " \2726"; color: var(--ink); font-size: 11px; }
  .card-back .divider { left: 345px; top: 60px; height: 130px; }
  .card-back .brand-name { position: absolute; left: 362px; top: 96px; width: 160px; font-size: 18px; }
</style>
</head>
<body>
<main class="canvas">
  <section class="card card-front" aria-label="Business card front">
    <div class="brand-name">Birchline Septic Solutions</div>
    <div class="divider"></div>
    <div class="contact">
      <div class="contact-name">Colin Vandro</div>
      <div class="contact-role">Owners</div>
      <div class="contact-line">
        <svg viewBox="0 0 24 24" aria-hidden="true"><path d="M6.6 10.8a15.1 15.1 0 0 0 6.6 6.6l2.2-2.2c.3-.3.7-.4 1-.2 1.1.4 2.3.6 3.6.6.6 0 1 .4 1 1V20c0 .6-.4 1-1 1A17 17 0 0 1 3 4c0-.6.4-1 1-1h3.5c.6 0 1 .4 1 1 0 1.3.2 2.5.6 3.6.1.3 0 .7-.2 1z"/></svg>
        <span>555-241-0387</span>
      </div>
      <div class="contact-line">
        <svg viewBox="0 0 24 24" aria-hidden="true"><path d="M12 2a7 7 0 0 0-7 7c0 5.3 7 13 7 13s7-7.7 7-13a7 7 0 0 0-7-7zm0 9.5a2.5 2.5 0 1 1 0-5 2.5 2.5 0 0 1 0 5z"/></svg>
        <span>Millbrook, OH</span>
      </div>
    </div>
    <div class="scene" role="img" aria-label="Black silhouette of pine trees and mountain ridges along the bottom of the card"></div>
  </section>

  <section class="card card-back" aria-label="Business card back">
    <div class="scene" role="img" aria-label="Black silhouette of a mountain peak and pine trees on the left side"></div>
    <div class="services">
      <div class="services-title">Our Services</div>
      <ul class="services-list">
        <li>Pumping</li>
        <li>Inspections</li>
        <li>Installs</li>
        <li>And Repairs</li>
      </ul>
    </div>
    <div class="divider"></div>
    <div class="brand-name">Birchline Septic Solutions</div>
  </section>
</main>
</body>
</html>
```